Business Card Design

I already have a company logo for my company. I have a logo for the manufacturer we represent. I want a professional business card design.

```html
<!DOCTYPE html>
<html lang="en">
<head>
<meta charset="utf-8">
<title>Beacon Alert Co. — Business Card</title>
<link rel="stylesheet" href="https://fonts.googleapis.com/css2?family=Open+Sans:wght@400;600;700&display=swap">
<style>
  :root {
    --backdrop: #202020;
    --card-gold: #b78c2e;
    --card-black: #1c1c21;
    --brand-red: #e01f27;
    --brand-orange: #e86a2c;
    --text-light: #ffffff;
    --card-w: 540px;
    --card-h: 310px;
    --radius: 18px;
  }
  * { box-sizing: border-box; margin: 0; padding: 0; }
  html, body {
    width: 1200px;
    height: 780px;
    overflow: hidden;
    background: var(--backdrop);
    font-family: "Open Sans", Arial, sans-serif;
  }
  .card-spread {
    position: absolute;
    inset: 0;
    display: flex;
    align-items: center;
    justify-content: center;
    gap: 40px;
  }
  .card {
    position: relative;
    width: var(--card-w);
    height: var(--card-h);
    border-radius: var(--radius);
    overflow: hidden;
    box-shadow: 0 14px 30px rgba(0,0,0,0.45);
  }

  /* Front */
  .card-front { background: var(--card-gold); }
  .front-shapes { position: absolute; inset: 0; width: 100%; height: 100%; }
  .contact-block {
    position: absolute;
    left: 34px;
    top: 34px;
    color: var(--text-light);
  }
  .person-name {
    font-size: 25px;
    font-weight: 700;
    line-height: 1.1;
  }
  .person-name .first-name { color: var(--brand-red); }
  .person-title {
    font-size: 14px;
    font-weight: 400;
    margin-top: 4px;
  }
  .address {
    font-size: 12.5px;
    line-height: 1.45;
    margin-top: 16px;
    font-style: normal;
  }
  .contact-list {
    list-style: none;
    margin-top: 14px;
    font-size: 12.5px;
    line-height: 1.5;
  }
  .contact-list li { display: flex; align-items: center; gap: 8px; }
  .contact-icon { width: 12px; height: 12px; fill: var(--brand-red); flex: none; }

  .front-brand {
    position: absolute;
    right: 34px;
    top: 150px;
    display: flex;
    align-items: center;
    gap: 10px;
  }
  .brand-dot {
    width: 16px; height: 16px;
    border-radius: 50%;
    background: var(--brand-red);
  }
  .brand-name {
    font-size: 22px;
    font-weight: 700;
    color: var(--text-light);
    letter-spacing: 0.5px;
  }

  /* Back */
  .card-back { background: var(--brand-red); }
  .back-pattern {
    position: absolute;
    inset: 0;
    background: linear-gradient(115deg, #dd1f26 0%, #e0252a 45%, #e4502c 80%, var(--brand-orange) 100%);
  }
  .back-brand {
    position: absolute;
    right: 30px;
    bottom: 26px;
    font-size: 11px;
    font-weight: 700;
    color: var(--text-light);
    letter-spacing: 0.4px;
  }
</style>
</head>
<body>
<main class="card-spread">

  <section class="card card-front" aria-label="Card front">
    <svg class="front-shapes" viewBox="0 0 540 310" preserveAspectRatio="none" aria-hidden="true">
      <path class="swoosh-shadow" fill="#1c1c21" d="M196,0 C300,10 300,190 400,260 C440,288 480,304 540,310 L540,0 Z" transform="translate(-14,0)"/>
      <path class="swoosh-red" fill="#e01f27" d="M196,0 C300,10 300,190 400,260 C440,288 480,304 540,310 L540,0 Z" transform="translate(-6,0)"/>
      <path class="field-black" fill="#1c1c21" d="M212,0 C316,10 314,186 412,254 C452,282 490,298 540,302 L540,0 Z"/>
    </svg>

    <div class="contact-block">
      <h1 class="person-name"><span class="first-name">Marena</span> Holloway</h1>
      <p class="person-title">Managing Director</p>
      <address class="address">418 Lantern Ridge Rd. Suite 120<br>Cedar Falls, TX 75000</address>
      <ul class="contact-list">
        <li>
          <svg class="contact-icon" viewBox="0 0 24 24" aria-hidden="true"><path d="M6.6 10.8a15.1 15.1 0 0 0 6.6 6.6l2.2-2.2a1 1 0 0 1 1-.25 11.4 11.4 0 0 0 3.6.57 1 1 0 0 1 1 1V20a1 1 0 0 1-1 1A17 17 0 0 1 3 4a1 1 0 0 1 1-1h3.5a1 1 0 0 1 1 1c0 1.25.2 2.45.57 3.57a1 1 0 0 1-.25 1z"/></svg>
          (555) 014-2290
        </li>
        <li>
          <svg class="contact-icon" viewBox="0 0 24 24" aria-hidden="true"><path d="M2 5h20v14H2zm2 2v.5l8 5 8-5V7zm0 2.8V17h16V9.8l-8 5z"/></svg>
          hello@beaconalert.example
        </li>
        <li>
          <svg class="contact-icon" viewBox="0 0 24 24" aria-hidden="true"><path d="M12 2a10 10 0 1 0 0 20 10 10 0 0 0 0-20zm6.9 6h-3a15.7 15.7 0 0 0-1.4-3.6A8 8 0 0 1 18.9 8zM12 4c.8 1.2 1.5 2.5 1.9 4h-3.8c.4-1.5 1.1-2.8 1.9-4zM4.3 14a8 8 0 0 1 0-4h3.4a16 16 0 0 0 0 4zm.8 2h3a15.7 15.7 0 0 0 1.4 3.6A8 8 0 0 1 5.1 16zm3-8h-3a8 8 0 0 1 4.4-3.6A15.7 15.7 0 0 0 8.1 8zM12 20c-.8-1.2-1.5-2.5-1.9-4h3.8c-.4 1.5-1.1 2.8-1.9 4zm2.3-6H9.7a14.6 14.6 0 0 1 0-4h4.6a14.6 14.6 0 0 1 0 4zm.2 5.6a15.7 15.7 0 0 0 1.4-3.6h3a8 8 0 0 1-4.4 3.6zm1.8-5.6a16 16 0 0 0 0-4h3.4a8 8 0 0 1 0 4z"/></svg>
          www.beaconalert.example
        </li>
      </ul>
    </div>

    <div class="front-brand">
      <span class="brand-dot" aria-hidden="true"></span>
      <span class="brand-name">Beacon Alert Co.</span>
    </div>
  </section>

  <section class="card card-back" aria-label="Card back">
    <div class="back-pattern" role="img" aria-label="Repeating brand-symbol pattern in red fading to orange"></div>
    <span class="back-brand">Beacon Alert Co.</span>
  </section>

</main>
</body>
</html>
```